Kestrel Home Business Card Design

We need a business card for a Building company based in Queensland, Australia. Our colours are orange black and we do base all our homes design names and other aspect of our business on astrology. We want the consumer to perceive the company as professional and to attract investors to our company.We have over 20 years in the building industry.We pride ourselves on our innovation of designs and making the building process for anyone from families to investor a smooth and simple experience.
Business
Amelia Prichard0411752116PO Box 454, Mudgeerbaameliaprichard@zodiachomes.com

```html
<!DOCTYPE html>
<html lang="en">
<head>
<meta charset="utf-8">
<title>Kestrel Homes Business Card</title>
<link href="https://fonts.googleapis.com/css2?family=League+Spartan:wght@700&family=Questrial&family=Open+Sans:wght@400;600&display=swap" rel="stylesheet">
<style>
  :root {
    --backdrop: #e8ebed;
    --card: #ffffff;
    --orange: #f7850f;
    --ink: #1b1b1b;
    --shadow: rgba(0, 0, 0, 0.12);
  }
  * { box-sizing: border-box; margin: 0; padding: 0; }
  html, body { width: 1200px; height: 900px; overflow: hidden; }
  body { background: var(--backdrop); position: relative; }

  .card {
    position: absolute;
    left: 250px;
    width: 700px;
    height: 400px;
    background: var(--card);
    overflow: hidden;
    box-shadow: 0 6px 18px var(--shadow);
  }
  .card--front { top: 30px; }
  .card--back { top: 470px; }

  .band { position: absolute; background: var(--orange); }
  .card--front .band { left: 92px; top: 0; width: 78px; height: 100%; }
  .card--back .band { left: 0; top: 112px; width: 100%; height: 78px; }

  .brand-dot {
    position: absolute;
    border-radius: 50%;
    background: var(--ink);
    border: 5px solid var(--card);
  }
  .card--front .brand-dot { left: 76px; top: 166px; width: 110px; height: 110px; }
  .card--back .brand-dot { left: 236px; top: 86px; width: 130px; height: 130px; }

  .wordmark {
    position: absolute;
    font-family: "League Spartan", sans-serif;
    font-weight: 700;
    color: var(--ink);
    white-space: nowrap;
    letter-spacing: -0.5px;
  }
  .card--front .wordmark { left: 202px; top: 150px; font-size: 44px; }
  .card--back .wordmark { left: 150px; top: 248px; font-size: 66px; }

  .divider {
    position: absolute;
    left: 186px;
    top: 236px;
    width: 296px;
    height: 2px;
    background: var(--orange);
  }
  .holder-name {
    position: absolute;
    right: 40px;
    top: 202px;
    font-family: "Questrial", sans-serif;
    font-size: 25px;
    color: var(--ink);
    white-space: nowrap;
  }
  .contact {
    position: absolute;
    right: 40px;
    top: 248px;
    text-align: right;
    font-family: "Open Sans", sans-serif;
    font-size: 13.5px;
    line-height: 1.55;
    color: var(--ink);
    list-style: none;
    white-space: nowrap;
  }
  .contact .email { font-weight: 600; }
</style>
</head>
<body>
  <section class="card card--front" aria-label="Business card front">
    <div class="band"></div>
    <div class="brand-dot"></div>
    <div class="wordmark">Kestrel Homes</div>
    <div class="divider"></div>
    <div class="holder-name">Harriet Colvane</div>
    <ul class="contact">
      <li class="phone">0487309625</li>
      <li class="address">PO Box 872, Tallowvale</li>
      <li class="email">harrietcolvane@kestrelhomes.example</li>
    </ul>
  </section>

  <section class="card card--back" aria-label="Business card back">
    <div class="band"></div>
    <div class="brand-dot"></div>
    <div class="wordmark">Kestrel Homes</div>
  </section>
</body>
</html>
```